Specialized Personal Trainer Needs a Business Card Design

I need a business card design for my personal training business called Tall Oak Fitness. I have my Human Kinetics degree in Exercise Science from the Halvering Polytechnic Institute as well as an extra certification from NFBP (National Federation of Body Practice). I work as a Cardiac Rehab Exercise Specialist and personal trainer giving specialized exercise prescriptions to those that have different heart conditions as well as work with the general population in weight loss, strength and conditioning, getting/staying fit.
Updates

I decided that I wanted a logo (as I did not have one before I submitted my project for a business card) so I am submitting a project to get a logo done and then I will decide on a business card, hopefully being able to use one of the designs already submitted.  My apologies for doing this backwards.  I am new to this so I appreciate your patience.

Thank you.

Hi, I have just created a project for a logo design (I realized I needed a logo and I should've done that first..oops!), please feel free to participate.  Once I receive a logo I like I will finalize my business card project and hopefully incorporate it into one of your business card designs. 

Thank you!

Target Market(s)

Business professionals

Industry/Entity Type

Personal Trainer

Requirements
Must have
• My name with my info:
Delphine R. Ashcroft (BHK)
NFBP Certified Clinical Exercise Specialist & Personal Trainer
del.ashcroft@talloakfitness.example
Cell: 555-302-6148

Please make it double sided.
Nice to have
• An image that represents cardiac and general fitness training.

```html
<!DOCTYPE html>
<html lang="en">
<head>
<meta charset="utf-8">
<title>Tall Oak Fitness — Business Card</title>
<link rel="stylesheet" href="https://fonts.googleapis.com/css2?family=Barlow:wght@400;800&family=Roboto+Condensed:wght@400;700&display=swap">
<style>
  :root {
    --brand-red: #e31b37;
    --paper: #ffffff;
    --ink: #111111;
    --edge: #d9d9d9;
    --shadow: rgba(0, 0, 0, 0.18);
  }
  html, body {
    margin: 0;
    padding: 0;
    width: 1200px;
    height: 901px;
    overflow: hidden;
    background: var(--paper);
  }
  .canvas {
    position: relative;
    width: 1200px;
    height: 901px;
  }
  .card {
    position: absolute;
    left: 269px;
    width: 712px;
    height: 407px;
    border-radius: 40px;
    box-shadow: 0 5px 8px var(--shadow);
    overflow: hidden;
  }
  .card--front {
    top: 43px;
    background: var(--brand-red);
    display: flex;
    align-items: center;
    justify-content: center;
  }
  .wordmark {
    margin: 0;
    color: var(--paper);
    font-family: "Barlow", sans-serif;
    font-weight: 800;
    font-size: 74px;
    line-height: 0.95;
    text-align: center;
    letter-spacing: -1px;
  }
  .card--back {
    top: 490px;
    background: var(--paper);
    border: 1px solid var(--edge);
    box-sizing: border-box;
    color: var(--ink);
  }
  .services {
    position: absolute;
    top: 50px;
    left: 0;
    right: 0;
    margin: 0;
    text-align: center;
    font-family: "Barlow", sans-serif;
    font-size: 19px;
    letter-spacing: 1.6px;
    word-spacing: 2px;
  }
  .services .divider { margin: 0 14px; }
  .identity {
    position: absolute;
    top: 138px;
    left: 0;
    right: 0;
    text-align: center;
    font-family: "Roboto Condensed", sans-serif;
  }
  .business-name {
    margin: 0;
    font-weight: 700;
    font-size: 42px;
    line-height: 1.15;
  }
  .person-name {
    margin: 8px 0 0;
    font-size: 31px;
    line-height: 1.1;
  }
  .person-name .credential { font-size: 23px; }
  .certification {
    margin: 4px 0 0;
    font-size: 21px;
  }
  .contact {
    position: absolute;
    left: 31px;
    bottom: 25px;
    margin: 0;
    font-family: "Roboto Condensed", sans-serif;
    font-size: 23px;
    line-height: 28.5px;
    font-style: normal;
  }
  .contact span { display: block; }
</style>
</head>
<body>
  <main class="canvas">
    <section class="card card--front" aria-label="Card front">
      <h1 class="wordmark">TALL OAK<br>FITNESS</h1>
    </section>

    <section class="card card--back" aria-label="Card back">
      <p class="services">TRAINING<span class="divider">|</span>CARDIAC REHABILITATION<span class="divider">|</span>WELLNESS</p>
      <div class="identity">
        <h2 class="business-name">Tall Oak Fitness</h2>
        <p class="person-name">Delphine R. Ashcroft <span class="credential">(BHK)</span></p>
        <p class="certification">NFBP Certified Clinical Exercise Specialist &amp; Personal Trainer</p>
      </div>
      <address class="contact">
        <span class="phone">555-302-6148</span>
        <span class="website">www.talloakfitness.example</span>
        <span class="email">del.ashcroft@talloakfitness.example</span>
      </address>
    </section>
  </main>
</body>
</html>
```